Design a modern, classy & professional business card for an online real estate agency, specializing in medium-luxury properties in Thailand and later in Singapore and UK.

Possible design ideas so far: (not essential)

- curved corner(s) to the card, white on front & turquoise on back or visa versa.

- front of card - clear and simple, company name in metallic grey/monochrome, logo graphic & company name on front in spot UV or embossed/debossed effect.

- back of card - large, close-cropped, 'ghost' patterns of the C-shaped curves of logo, or company name repeated on back of card in spot UV.

Target Market(s)

- young to middle-aged professionals mainly (but ideally should design should suit all)

- UK, US,EU,AUS & ASIAN mainly (but ideally should design should suit all countries)

Industry/Entity Type

Real Estate

Requirements
Must have
• THEME:
- Luxurious & Modern
- Clean & striking
- Unique & creative

INFO:
- Logo & company name on front
- Contact details on back:

Tobias Hennlund
Managing Director

www.velmontestates.asia
www.velmontestates.co.uk

Tel: 083-274-6159
email: tobias@velmontestates.asia

(contact details can be displayed in any order as suites design.)

Nice to have
• - curved corner(s) to the card, white on front & turquoise on back or visa versa.

Should not have
• - No generic images of properties, palm trees/coconut trees etc.

- No other other bold colors, except for main turquoise, grey, metallic white & black theme.

- No obvious business card templates

```html
<!DOCTYPE html>
<html lang="en">
<head>
<meta charset="utf-8">
<title>Velmont Estates – Business Card</title>
<link href="https://fonts.googleapis.com/css2?family=Open+Sans:wght@400;600;700&display=swap" rel="stylesheet">
<style>
  :root {
    --backdrop: #dcdfe3;
    --card-white: #f4f5f6;
    --turquoise: #12c8c8;
    --crescent-grey: #777879;
    --brand-grey: #7a7b7d;
    --ink: #1f2a30;
    --ink-soft: #23343a;
  }
  * { margin: 0; padding: 0; box-sizing: border-box; }
  html, body {
    width: 1200px;
    height: 865px;
    overflow: hidden;
    background: var(--backdrop);
    font-family: "Open Sans", Arial, sans-serif;
  }
  .business-card {
    position: absolute;
    left: 100px;
    top: 146px;
    width: 1000px;
    height: 572px;
    background: var(--turquoise);
    overflow: hidden;
    box-shadow: 0 14px 34px rgba(0, 0, 0, 0.18);
  }
  .card-shapes {
    position: absolute;
    inset: 0;
    width: 100%;
    height: 100%;
  }
  .brand-mark {
    position: absolute;
    left: 190px;
    top: 150px;
    width: 118px;
    height: 118px;
    background: var(--turquoise);
  }
  .brand-name {
    position: absolute;
    left: 176px;
    top: 282px;
    color: var(--brand-grey);
    font-weight: 400;
    line-height: 1;
  }
  .brand-name .brand-primary {
    display: block;
    font-size: 78px;
    letter-spacing: -1px;
  }
  .brand-name .brand-secondary {
    display: block;
    margin-top: 8px;
    margin-left: 46px;
    font-size: 24px;
    letter-spacing: 9px;
  }
  .contact-block {
    position: absolute;
    right: 70px;
    top: 78px;
    text-align: right;
    color: var(--ink-soft);
  }
  .contact-name {
    font-size: 23px;
    font-weight: 700;
    color: var(--ink);
  }
  .contact-role {
    font-size: 20px;
    font-weight: 400;
    margin-bottom: 58px;
  }
  .contact-line {
    font-size: 19px;
    line-height: 1.45;
    display: flex;
    justify-content: flex-end;
    align-items: center;
    gap: 8px;
  }
  .contact-line svg {
    width: 17px;
    height: 17px;
    fill: var(--ink-soft);
  }
  .contact-address { margin-bottom: 6px; }
  .contact-gap { margin-top: 10px; }
</style>
</head>
<body>
  <div class="business-card">
    <svg class="card-shapes" viewBox="0 0 1000 572" aria-hidden="true">
      <defs>
        <radialGradient id="whiteGlow" cx="0.35" cy="0.35" r="0.8">
          <stop offset="0" stop-color="#ffffff"/>
          <stop offset="1" stop-color="#e9eaeb"/>
        </radialGradient>
      </defs>
      <path d="M0,0 L430,0 C650,40 730,240 655,380 C612,455 548,520 505,572 L0,572 Z" fill="url(#whiteGlow)"/>
      <path d="M598,160 C690,270 660,430 478,572 L440,572 C560,450 625,320 598,160 Z" fill="var(--crescent-grey)"/>
      <path d="M0,0 L430,0 C620,40 640,200 590,300 C550,390 490,480 430,572 L0,572 Z" fill="url(#whiteGlow)"/>
    </svg>

    <div class="brand-mark"></div>
    <div class="brand-name">
      <span class="brand-primary">Velmont</span>
      <span class="brand-secondary">ESTATES</span>
    </div>

    <div class="contact-block">
      <p class="contact-name">Marlow Finch-Avery</p>
      <p class="contact-role">Consultant</p>
      <p class="contact-line">041, 9th floor, Plaza</p>
      <p class="contact-line contact-address">Harbourside Road KTN</p>
      <p class="contact-line">014 267 3580
        <svg viewBox="0 0 24 24"><path d="M6.6 10.8a15.1 15.1 0 0 0 6.6 6.6l2.2-2.2a1 1 0 0 1 1-.25 11.4 11.4 0 0 0 3.6.57 1 1 0 0 1 1 1V20a1 1 0 0 1-1 1A17 17 0 0 1 3 4a1 1 0 0 1 1-1h3.5a1 1 0 0 1 1 1c0 1.25.2 2.45.57 3.57a1 1 0 0 1-.25 1z"/></svg>
      </p>
      <p class="contact-line">014 267 3580
        <svg viewBox="0 0 24 24"><path d="M5 3h9v5h5v13H5z M7 10h2v2H7z M11 10h2v2h-2z M15 10h2v2h-2z M7 14h2v2H7z M11 14h2v2h-2z M15 14h2v2h-2z" fill-rule="evenodd"/></svg>
      </p>
      <p class="contact-line">hello@inboxmail.com
        <svg viewBox="0 0 24 24"><path d="M2 5h20v14H2z M3.5 6.5 12 13l8.5-6.5" fill-rule="evenodd"/></svg>
      </p>
      <p class="contact-line contact-gap">hello@inboxmail.com</p>
      <p class="contact-line">www.yoursitename.net</p>
    </div>
  </div>
</body>
</html>
```